Conference flyer

We need a flyer for a conference for the defence industry. The attached has been updated with new information using last years flyer. We would like something new and fresh. Please note the theme of the conference is 'a global environment'.

The final design should reflect the defence industry and manufacturing.

Industry/Entity Type

Defence

```html
<!DOCTYPE html>
<html lang="en">
<head>
<meta charset="utf-8">
<title>Defence Trade Controls Annual Conference – Agenda</title>
<link rel="stylesheet" href="https://fonts.googleapis.com/css2?family=Open+Sans:wght@400;600;700&display=swap">
<style>
  :root {
    --stage: #1f1f1f;
    --paper: #ffffff;
    --ink: #222222;
    --title-blue: #2a3a94;
    --day-bar: #1b2b5e;
    --rule: #c9cdd6;
    --training-top: #0e1a3c;
    --training-body: #1c2f63;
    --module-tab: #3d63b8;
    --white: #ffffff;
  }
  * { box-sizing: border-box; margin: 0; padding: 0; }
  html, body {
    width: 913px; height: 1200px; overflow: hidden;
    background: var(--stage);
    font-family: "Open Sans", Arial, sans-serif;
  }
  .canvas { position: relative; width: 913px; height: 1200px; }
  .page-label {
    position: absolute; top: 52px; left: 0; width: 913px;
    text-align: center; color: var(--white);
    font-size: 35px; font-weight: 400;
  }
  .flyer {
    position: absolute; left: 76px; top: 147px;
    width: 763px; height: 984px; background: var(--paper);
  }
  .masthead {
    position: absolute; left: 0; top: 0; width: 763px; height: 142px;
    background:
      linear-gradient(180deg, rgba(255,255,255,0) 0%, rgba(255,255,255,0.85) 18%, rgba(255,255,255,0.85) 78%, rgba(255,255,255,0) 100%),
      linear-gradient(90deg, #3b55a8 0%, #8fa7d8 30%, #dfe7f5 55%, #7d98d0 80%, #2f4a9c 100%);
  }
  .masthead-title {
    position: absolute; left: 0; top: 20px; width: 763px;
    text-align: center; color: var(--title-blue);
    font-weight: 700; font-size: 37px; line-height: 48px; letter-spacing: 0.5px;
  }
  .day-bar {
    position: absolute; top: 169px; height: 39px;
    background: var(--day-bar); color: var(--white);
    font-weight: 700; font-size: 16px; line-height: 39px; text-align: center;
  }
  .day-bar.day-one { left: 15px; width: 348px; }
  .day-bar.day-two { left: 402px; width: 351px; }
  .column-rule {
    position: absolute; left: 383px; top: 171px; width: 1px; height: 518px;
    background: var(--rule);
  }
  .agenda { position: absolute; top: 216px; list-style: none; color: var(--ink); font-size: 13.2px; }
  .agenda.day-one { left: 19px; width: 350px; }
  .agenda.day-two { left: 404px; width: 355px; }
  .agenda li { display: flex; min-height: 27px; line-height: 20px; padding-top: 3.5px; }
  .agenda .time { width: 52px; flex: none; }
  .agenda .item { flex: 1; }
  .agenda li.topic .item { padding-left: 0; }
  .agenda li.close .time { padding-left: 3px; }
  .agenda li.close .item { padding-left: 3px; }
  .agenda-note {
    position: absolute; left: 19px; top: 681px;
    font-size: 10.5px; color: var(--ink);
  }
  .training {
    position: absolute; left: 0; top: 709px; width: 763px; height: 275px;
    background: var(--training-body); color: var(--white);
  }
  .training-globe {
    position: absolute; left: 420px; top: 44px; width: 343px; height: 231px;
    background: radial-gradient(ellipse at 75% 75%, #2d4b8f 0%, #22397a 45%, rgba(28,47,99,0) 75%);
  }
  .training-head {
    position: absolute; left: 0; top: 0; width: 763px; height: 44px;
    background: var(--training-top);
  }
  .training-title {
    position: absolute; left: 25px; top: 9px;
    font-size: 19.5px; font-weight: 700; letter-spacing: 0.2px;
  }
  .module-tab {
    position: absolute; left: 19px; height: 26px;
    background: var(--module-tab);
    font-size: 13.5px; font-weight: 700; line-height: 26px; padding-left: 9px;
  }
  .module-tab.pre { top: 61px; width: 302px; }
  .module-tab.post { top: 136px; width: 323px; }
  .session { position: absolute; left: 25px; font-size: 13px; display: flex; }
  .session .when { width: 137px; font-weight: 700; }
  .session.monday { top: 99px; }
  .session.thursday { top: 175px; }
  .session.module-three { top: 206px; }
  .session.friday { top: 238px; }
</style>
</head>
<body>
<div class="canvas">
  <div class="page-label">Page 2</div>

  <main class="flyer">
    <header class="masthead" role="img" aria-label="Header image: globe with light streaks in blues and white">
      <h1 class="masthead-title">DEFENCE TRADE CONTROLS<br>ANNUAL CONFERENCE</h1>
    </header>

    <h2 class="day-bar day-one">DAY 1: TUESDAY, 2 JUNE 2015</h2>
    <h2 class="day-bar day-two">DAY 2: WEDNESDAY, 3 JUNE 2015</h2>
    <div class="column-rule"></div>

    <ul class="agenda day-one">
      <li><span class="time">0830</span><span class="item">Registration</span></li>
      <li><span class="time">0900</span><span class="item">Chair’s welcome &amp; opening address</span></li>
      <li><span class="time">0915</span><span class="item">Australian Legislative Changes</span></li>
      <li><span class="time">0950</span><span class="item">Export Control Reform - next steps</span></li>
      <li><span class="time">1030</span><span class="item">Morning tea and networking</span></li>
      <li><span class="time">1100</span><span class="item">Managing Multi-jurisdictional Programs</span></li>
      <li><span class="time">1145</span><span class="item">Country Focus: Japan</span></li>
      <li><span class="time">1230</span><span class="item">Lunch</span></li>
      <li><span class="time">1330</span><span class="item">Export Control Reform &amp; FMS,<br>CoA management</span></li>
      <li><span class="time">1400</span><span class="item">Country Focus: Singapore</span></li>
      <li><span class="time">1430</span><span class="item">Customs Trusted Trader Program</span></li>
      <li><span class="time">1500</span><span class="item">Afternoon tea and networking</span></li>
      <li><span class="time">1530</span><span class="item">Industry Best practice panelLed<br>by: Daniel Hartley</span></li>
      <li><span class="time">1645</span><span class="item">Day one wrap up</span></li>
      <li><span class="time">1730</span><span class="item">Reception</span></li>
    </ul>

    <ul class="agenda day-two">
      <li><span class="time">0900</span><span class="item">Chair’s welcome back</span></li>
      <li><span class="time">0910</span><span class="item">Best Practice Compliance</span></li>
      <li><span class="time">0950</span><span class="item">Compliance Case Study</span></li>
      <li><span class="time">1030</span><span class="item">Morning tea and networking</span></li>
      <li><span class="time">1100</span><span class="item">Practical management of export control reform</span></li>
      <li><span class="time">1130</span><span class="item">EAR Exceptions - the good, the bad &amp; the ugly</span></li>
      <li><span class="time">1200</span><span class="item">Country Focus: European Union</span></li>
      <li><span class="time">1245</span><span class="item">Lunch and netowrking</span></li>
      <li><span class="time">1345</span><span class="item">Export Control - round table discussions</span></li>
      <li class="topic"><span class="time"></span><span class="item">- Dual national exemptions</span></li>
      <li class="topic"><span class="time"></span><span class="item">- Understanding ‘Specially Designed’</span></li>
      <li class="topic"><span class="time"></span><span class="item">- Deminimis</span></li>
      <li class="topic"><span class="time"></span><span class="item">- Re-exports under EAR</span></li>
      <li class="topic"><span class="time"></span><span class="item">- U.S. Trade Co-operation Treaty</span></li>
      <li class="topic"><span class="time"></span><span class="item">- Securing your supply chain</span></li>
      <li class="close"><span class="time">1500</span><span class="item">Conference Q&amp;A and wrap up</span></li>
      <li class="close"><span class="time">1530</span><span class="item">conference close</span></li>
    </ul>

    <p class="agenda-note">Note: agenda &amp; Presenters may vary without notice</p>

    <section class="training">
      <div class="training-globe" role="img" aria-label="Faint globe image in deep blue tones"></div>
      <div class="training-head">
        <h2 class="training-title">4 X HALF DAY PRE AND POST TRAINING SESSIONS</h2>
      </div>
      <h3 class="module-tab pre">PRE CONFERENCE TRAINING MODULES:</h3>
      <p class="session monday"><span class="when">Monday 1 June:</span><span>Module 1- Export Controls for Beginnners - helping beginners to make the best of the conference</span></p>
      <h3 class="module-tab post">POST CONFERENCE TRAINING MODULES:</h3>
      <p class="session thursday"><span class="when">Thursday 4 June:</span><span>Module 2- Practi management of export control reform</span></p>
      <p class="session module-three"><span class="when"></span><span>Module 3- Tips and Hints for best practice compliance</span></p>
      <p class="session friday"><span class="when">Friday 5 June:</span><span>Module 4- Making the best of Commerce exceptions</span></p>
    </section>
  </main>
</div>
</body>
</html>
```